Business Card for my New Brokerage

Looking to get a business card design for my new Real Estate Brokerage.
I want it with Picture, Phone Number, Email, Website, Office Address
Name and Designation. Please add logo too.

Target Market(s)

Real Estate Investors or Home Buyers

Industry/Entity Type

Real Estate

Contact Information for Business Card

Name, Email, Phone Number, website, email, office address

Colors
EB3D1F
EC4F4E
F09395
F8D3D4
FCEDEE

Requirements
Must have
• Minimalistic, Clean, Modern, Photo
Nice to have
• White and Red Colors

```html
<!DOCTYPE html>
<html lang="en">
<head>
<meta charset="utf-8">
<title>Ember Realty Inc – Business Card</title>
<link href="https://fonts.googleapis.com/css2?family=Montserrat:wght@400;500;700;800&display=swap" rel="stylesheet">
<style>
  :root {
    --brand-red: #e23a27;
    --brand-red-deep: #d8321f;
    --ink: #2a2a2a;
    --paper: #ffffff;
    --backdrop: #c9cccd;
    --photo-light: #f3ece6;
    --photo-mid: #c99b82;
    --photo-dark: #4a2c22;
  }
  * { box-sizing: border-box; margin: 0; padding: 0; }
  html, body {
    width: 1187px; height: 1200px; overflow: hidden;
    background: var(--backdrop);
    font-family: "Montserrat", sans-serif;
  }
  .card {
    position: absolute;
    border-radius: 16px;
    overflow: hidden;
  }
  /* Front */
  .card-front {
    left: 219px; top: 122px; width: 751px; height: 430px;
    background: var(--brand-red);
    color: var(--paper);
    text-align: center;
  }
  .brand {
    font-weight: 700;
    line-height: 1;
  }
  .brand-name { display: block; letter-spacing: 1px; }
  .brand-sub { display: block; letter-spacing: 5px; }
  .card-front .brand { position: absolute; left: 0; right: 0; top: 160px; }
  .card-front .brand-name { font-size: 82px; }
  .card-front .brand-sub { font-size: 22px; margin-top: 14px; }
  .card-front .site {
    position: absolute; left: 0; right: 0; top: 383px;
    font-size: 17px; font-weight: 500; letter-spacing: 1.4px;
  }
  /* Back */
  .card-back {
    left: 214px; top: 644px; width: 761px; height: 434px;
    background: var(--paper);
    color: var(--ink);
  }
  .card-back .brand {
    position: absolute; left: 51px; top: 50px;
    color: var(--brand-red); text-align: center;
  }
  .card-back .brand-name { font-size: 62px; }
  .card-back .brand-sub { font-size: 17px; margin-top: 10px; letter-spacing: 4px; }
  .agent { position: absolute; left: 52px; top: 198px; width: 360px; }
  .agent-name {
    color: var(--brand-red); font-weight: 800; font-size: 24px; letter-spacing: 0.5px;
  }
  .agent-role { font-size: 17px; font-weight: 500; margin-top: 4px; letter-spacing: 0.6px; }
  .rule { width: 58px; height: 3px; background: var(--brand-red-deep); margin: 5px 0 7px; }
  .address { font-size: 17px; font-weight: 500; line-height: 27px; letter-spacing: 0.5px; }
  .contact { list-style: none; margin-top: 4px; }
  .contact li {
    display: flex; align-items: center; gap: 8px;
    font-size: 17px; font-weight: 500; letter-spacing: 0.6px; height: 29px;
  }
  .contact svg { width: 14px; height: 14px; flex: none; fill: var(--brand-red); }
  .agent-photo {
    position: absolute; right: 0; top: 0; width: 357px; height: 100%;
    background:
      radial-gradient(ellipse 45% 38% at 55% 38%, var(--photo-mid) 0 55%, transparent 70%),
      radial-gradient(ellipse 62% 55% at 55% 40%, var(--photo-dark) 0 60%, transparent 75%),
      linear-gradient(180deg, var(--paper) 0%, var(--paper) 55%, var(--photo-light) 70%, var(--photo-light) 100%);
  }
</style>
</head>
<body>
  <section class="card card-front">
    <div class="brand" aria-label="Ember Realty Inc">
      <span class="brand-name">EMBER</span>
      <span class="brand-sub">REALTY INC</span>
    </div>
    <p class="site">www.emberrealtyinc.com</p>
  </section>

  <section class="card card-back">
    <div class="brand" aria-label="Ember Realty Inc">
      <span class="brand-name">EMBER</span>
      <span class="brand-sub">REALTY INC</span>
    </div>
    <div class="agent">
      <h1 class="agent-name">CLAIRE MARLOWE</h1>
      <p class="agent-role">Broker Associate</p>
      <div class="rule"></div>
      <p class="address">204 Harbor Point Complex<br>Riverside Business Park</p>
      <div class="rule"></div>
      <ul class="contact">
        <li>
          <svg viewBox="0 0 16 16" aria-hidden="true"><path d="M3.6 1.2l2.3 2.6-1.3 2.1c.9 1.9 2.4 3.4 4.3 4.4l2.1-1.3 2.6 2.3-1.2 2.4C7.2 13.6 2.4 8.8 1.2 2.4z"/></svg>
          401-555-0142
        </li>
        <li>
          <svg viewBox="0 0 16 16" aria-hidden="true"><path d="M1 3h14v10H1z M2 4l6 5 6-5" stroke="#fff" stroke-width="1.2"/></svg>
          hello@emberrealtyinc.com
        </li>
        <li>
          <svg viewBox="0 0 16 16" aria-hidden="true"><circle cx="8" cy="8" r="7"/><path d="M1 8h14M8 1v14M3 4.5h10M3 11.5h10M8 1c-3 3-3 11 0 14M8 1c3 3 3 11 0 14" stroke="#fff" stroke-width="0.9" fill="none"/></svg>
          www.emberrealtyinc.com
        </li>
      </ul>
    </div>
    <div class="agent-photo" role="img" aria-label="Portrait photo of the broker associate"></div>
  </section>
</body>
</html>
```